Advert for Services that we offer

Brimfold Haulage Ltd need an design to represent what we do in a modern way by showing an image with a brief description and the use of corporate logo the information we will proved vie a doc file and this is to be presented in a modern way. This design will be for print & web. we have done our own design and its not great i have put this in the file repository

Target Market(s)

Motor trade

Font styles to use
Sans Serif

Colors

Designer to choose colors to be used in the design.

Requirements
Must have
• Company colour scheme as per logo within the files uploaded.
• and a small boarder to isolate it from the rest of the articles.
Nice to have
• Modern font
Should not have
• Old style font

```html
<!DOCTYPE html>
<html lang="en">
<head>
<meta charset="utf-8">
<title>Brimfold Haulage Ltd – Product Testing and Analysis</title>
<link href="https://fonts.googleapis.com/css2?family=Bebas+Neue&family=Open+Sans:wght@400;600&display=swap" rel="stylesheet">
<style>
  :root {
    --brand-blue: #1c6dbd;
    --pill-blue: #2c86d6;
    --text-grey: #3b4048;
    --bg-white: #ffffff;
    --bg-ice: #e6f3fc;
    --bg-sky: #9fd3f4;
    --photo-dark: #3a3d42;
    --photo-rust: #a9573a;
  }
  * { margin: 0; padding: 0; box-sizing: border-box; }
  html, body { width: 1200px; height: 775px; overflow: hidden; background: var(--bg-white); }
  .advert {
    position: relative;
    width: 1200px;
    height: 775px;
    overflow: hidden;
    background:
      radial-gradient(ellipse at 85% 95%, var(--bg-sky) 0%, rgba(159,211,244,0) 45%),
      radial-gradient(ellipse at 20% 10%, var(--bg-sky) 0%, rgba(159,211,244,0) 40%),
      linear-gradient(135deg, var(--bg-ice) 0%, var(--bg-white) 55%, var(--bg-ice) 100%);
    font-family: "Open Sans", Arial, sans-serif;
  }
  .service-photo { position: absolute; left: 0; top: 0; width: 540px; height: 775px; }
  .brand {
    position: absolute;
    left: 262px;
    top: 140px;
    display: flex;
    align-items: center;
    gap: 9px;
    white-space: nowrap;
    font-family: "Bebas Neue", Arial, sans-serif;
    font-size: 26px;
    letter-spacing: 1px;
    color: var(--brand-blue);
    line-height: 1;
  }
  .brand-square { width: 20px; height: 20px; background: var(--brand-blue); flex: none; }
  .divider {
    position: absolute;
    left: 541px;
    top: 90px;
    width: 1px;
    height: 137px;
    background: var(--text-grey);
    opacity: 0.6;
  }
  .headline {
    position: absolute;
    left: 588px;
    top: 84px;
    font-family: "Bebas Neue", Arial, sans-serif;
    font-weight: 400;
    font-size: 80px;
    line-height: 72px;
    letter-spacing: 1px;
    color: var(--brand-blue);
  }
  .services {
    position: absolute;
    left: 604px;
    top: 249px;
    list-style: none;
    font-family: "Bebas Neue", Arial, sans-serif;
    font-size: 36px;
    line-height: 54.8px;
    letter-spacing: 1.6px;
    color: var(--text-grey);
  }
  .services li { position: relative; padding-left: 22px; }
  .services li::before {
    content: "";
    position: absolute;
    left: 0;
    top: 24px;
    width: 6px;
    height: 6px;
    border-radius: 50%;
    background: var(--text-grey);
  }
  .contact {
    position: absolute;
    left: 596px;
    top: 642px;
    width: 519px;
    height: 47px;
    border: 2px solid var(--pill-blue);
    border-radius: 24px;
    display: flex;
    align-items: center;
    font-size: 18px;
    font-weight: 600;
    color: var(--brand-blue);
  }
  .contact-web { width: 309px; text-align: center; }
  .contact-sep { width: 1px; height: 24px; background: var(--brand-blue); }
  .contact-phone { flex: 1; text-align: center; }
</style>
</head>
<body>
  <main class="advert">
    <svg class="service-photo" viewBox="0 0 540 775" role="img" aria-label="Photo of a technician measuring the bore of a large flanged casting with a digital dial gauge">
      <defs>
        <linearGradient id="photo-tone" x1="0" y1="1" x2="1" y2="0">
          <stop offset="0" stop-color="var(--photo-dark)"/>
          <stop offset="0.35" stop-color="var(--photo-rust)"/>
          <stop offset="0.62" stop-color="var(--photo-rust)" stop-opacity="0.25"/>
          <stop offset="0.8" stop-color="var(--photo-rust)" stop-opacity="0"/>
        </linearGradient>
      </defs>
      <rect x="0" y="0" width="540" height="775" fill="url(#photo-tone)"/>
    </svg>

    <div class="brand">
      <span class="brand-square"></span>
      <span class="brand-name">Brimfold Haulage Ltd</span>
    </div>

    <div class="divider"></div>

    <h1 class="headline">Product Testing<br>and Analysis</h1>

    <ul class="services">
      <li>Metallurgical Testing</li>
      <li>Bearing Pre-Load Testing</li>
      <li>Bore Measurement</li>
      <li>New Product Evaluation</li>
      <li>Product Analysis &amp; Report</li>
    </ul>

    <div class="contact">
      <span class="contact-web">www.brimfold-haulage.co.uk</span>
      <span class="contact-sep"></span>
      <span class="contact-phone">0161 496 0725</span>
    </div>
  </main>
</body>
</html>
```